Business Card Design

We would like to re-design our business cards. Our Company - Qwinrel Turbochargers, rebuilds turbochargers and sells replacement parts. Our website is: http://www.qwinrelturbochargers-example.com
We just had our logo changed. I will attach the file. Looking for fresh new/modern business card. We like the colors red, black, white and silver. Black background looks attractive, but not a requirement. The final design should communicate reasonable/competitive prices, top quality and reliability of our products.
Updates
Project Deadline Extended
Reason: Need to finalize the info on the card. Currently working on changing address and email info. Want to make sure it is the correct one before accepting the final design. Unless, this is something that can be changed at a later time..??
Industry/Entity Type
Business
Contact Information for Business Card
QWINREL TURBOCHARGERS, LLC
20473 Harwick Lane NE
Massillon, OH 44647
Tel: +1-555-214-7390
Fax: +1-555-267-1842
info@QwinrelTurbochargers-example.com
Our current business card had the following highlights:
*We rebuild all Turbocharges for Automotive, Diesel and Industrial
*Precision Balancing and in-house turbocharger needs
*All Turbocharger replacement parts are made in USA / U.K.
Look and feel
Each slider illustrates characteristics of the customer's brand and the style your logo design should communicate.

```html
<!DOCTYPE html>
<html lang="en">
<head>
<meta charset="utf-8">
<title>Qwinrel Turbochargers – Business Cards</title>
<link rel="stylesheet" href="https://fonts.googleapis.com/css2?family=Open+Sans:wght@400;600;700;800&display=swap">
<style>
  :root {
    --bg: #e9e6e1;
    --card-white: #fbfbfb;
    --red: #e8242f;
    --red-deep: #c7141f;
    --ink: #1f1f1f;
    --silver: #b9b9b9;
    --black: #111111;
    --black-soft: #262626;
    --white: #ffffff;
  }
  * { margin: 0; padding: 0; box-sizing: border-box; }
  html, body {
    width: 1200px; height: 1023px; overflow: hidden;
    background: var(--bg);
    font-family: "Open Sans", Arial, sans-serif;
  }
  .canvas { position: relative; width: 1200px; height: 1023px; }

  .card {
    position: absolute; width: 640px; height: 366px;
    border-radius: 4px; overflow: hidden;
    box-shadow: 0 10px 28px rgba(0,0,0,.22);
  }
  .card-front { left: 60px; top: 70px; background: var(--card-white); }
  .card-back  { left: 500px; top: 587px;
    background: linear-gradient(135deg, var(--black-soft), var(--black)); }

  .card-art { position: absolute; inset: 0; width: 100%; height: 100%; }

  .brand { position: absolute; display: flex; align-items: center; gap: 10px; }
  .brand-dot { width: 34px; height: 34px; border-radius: 50%; background: var(--red); flex: none; }
  .brand-name { font-weight: 800; font-size: 23px; letter-spacing: .2px; }
  .card-front .brand { left: 44px; top: 70px; }
  .card-front .brand-name { color: var(--ink); }

  .person { position: absolute; left: 44px; top: 140px; }
  .person-name { color: var(--red); font-size: 25px; font-weight: 400; line-height: 1.1; }
  .person-role { color: var(--ink); font-size: 13px; margin-top: 4px; }

  .contacts { position: absolute; left: 64px; top: 262px; list-style: none; }
  .contacts li {
    display: flex; align-items: center; gap: 10px;
    color: var(--white); font-size: 13.5px; line-height: 21px;
  }
  .contacts svg { width: 13px; height: 13px; flex: none; fill: var(--white); }

  .address {
    position: absolute; right: 30px; top: 36px; text-align: right;
    color: var(--white); font-size: 15px; line-height: 22px;
  }

  .card-back .brand { left: 210px; top: 150px; }
  .card-back .brand-name { color: var(--white); font-size: 26px; }
  .card-back .brand-dot { width: 40px; height: 40px; }
  .site {
    position: absolute; left: 0; right: 0; top: 232px; text-align: center;
    color: var(--white); font-size: 15px;
  }
  .site .accent { color: var(--red); }
</style>
</head>
<body>
<main class="canvas">

  <section class="card card-front" aria-label="Business card front">
    <svg class="card-art" viewBox="0 0 640 366" preserveAspectRatio="none" aria-hidden="true">
      <defs>
        <linearGradient id="redFill" x1="0" y1="0" x2="1" y2="1">
          <stop offset="0" stop-color="#f0323c"/>
          <stop offset="1" stop-color="#c7141f"/>
        </linearGradient>
      </defs>
      <path d="M452 0 C 380 120, 230 215, 0 262 L0 366 L640 366 L640 0 Z" fill="url(#redFill)"/>
      <path d="M440 0 C 368 118, 220 208, 0 250" fill="none" stroke="#b9b9b9" stroke-width="3"/>
      <path d="M448 0 C 376 120, 226 213, 0 257" fill="none" stroke="#111" stroke-width="6"/>
    </svg>

    <div class="brand">
      <span class="brand-dot"></span>
      <span class="brand-name">Qwinrel Turbochargers</span>
    </div>

    <div class="person">
      <p class="person-name">Lorren Vask</p>
      <p class="person-role">Director</p>
    </div>

    <ul class="contacts">
      <li><svg viewBox="0 0 16 16"><path d="M3 1h3l1.5 4-2 1.3a9 9 0 0 0 4.2 4.2L11 8.5l4 1.5v3a2 2 0 0 1-2 2A12 12 0 0 1 1 3a2 2 0 0 1 2-2z"/></svg>+1-555-214-7390</li>
      <li><svg viewBox="0 0 16 16"><path d="M4 1h7v4H4zM2 6h12v6h-2v3H4v-3H2zM5 10v4h6v-4z"/></svg>+1-555-267-1842</li>
      <li><svg viewBox="0 0 16 16"><path d="M1 3h14v10H1zM2 4.5v.3l6 4 6-4v-.3z"/></svg>info@QwinrelTurbochargers-example.com</li>
      <li><svg viewBox="0 0 16 16"><path d="M8 1a7 7 0 1 0 0 14A7 7 0 0 0 8 1zm0 1.5c.8 1 1.3 2.5 1.4 4.5H6.6C6.7 5 7.2 3.5 8 2.5zM2.6 7h2.5c.1-1.6.4-3 1-4A5.5 5.5 0 0 0 2.6 7zm0 2a5.5 5.5 0 0 0 3.5 4c-.6-1-.9-2.4-1-4zm4 0c.1 2 .6 3.5 1.4 4.5.8-1 1.3-2.5 1.4-4.5zm4.3 0c-.1 1.6-.4 3-1 4a5.5 5.5 0 0 0 3.5-4zm0-2h2.5a5.5 5.5 0 0 0-3.5-4c.6 1 .9 2.4 1 4z"/></svg>www.qwinrelturbochargers-example.com</li>
    </ul>

    <address class="address" style="font-style:normal">
      7182 Brindlemoor Ave. NW<br>
      North Calderby, Ohio
    </address>
  </section>

  <section class="card card-back" aria-label="Business card back">
    <div class="brand">
      <span class="brand-dot"></span>
      <span class="brand-name">Qwinrel Turbochargers</span>
    </div>
    <p class="site">www.<span class="accent">qwinrelturbochargers-example</span>.com</p>
  </section>

</main>
</body>
</html>
```